Launching a new real estate agency in Monaco

Hello, I am opening a new real estate agency in Monaco. For the purpose of my activity, in order to be known quickly among a fierce competition I need an advertising campaign that will be broadcast in local magazines, newspapers, paper board, etc.

You will find example of pictures of Monaco on which I have the rights and my logo. You can always pick other images that I can buy if the price is reasonable for a commercial use (<200 $)

Please respect the color code.

I wish you good luck and look forward to give you my feedbacks

Reason: Only few projects posted were respecting the brief and of quality. Hoping to receive more in coming days

Target Market(s)

International high-end clientele of all ages, all genders.

Industry/Entity Type

Real Estate Agent

Font styles to use
Serif

Requirements
Must have
• 1/ My logo
• 2/ This message "Un nouveau regard sur l'immobilier" means in English a fresh look at real estate or new eyes on real-estate.
• 3/ My address: 14 rue des Ormeaux, Galerie Bellerive Nord, 98 000 Monaco
• 4/ Phone number: +377.93.48.25.07
• 5/ Website: www.corvano-immo.com.
• 6/ Format: Files should be easily adjustable but I'd like a vertical display to fit easily in Magazines, Poster and billboard. So please work in high resolution !
Nice to have
• Please think about your design in accordance with the message I want to display.
Should not have
• A simple poster with a picture of Monaco that does not take into consideration the message of the advertisement, "Un nouveau regard sur l'immobilier" which means in english, new eyes on real-estate or a new look at real-estate, or new vision at real-estate.

```html
<!DOCTYPE html>
<html lang="fr">
<head>
<meta charset="utf-8">
<title>Corvano Immo — Un nouveau regard sur l'immobilier</title>
<link rel="stylesheet" href="https://fonts.googleapis.com/css2?family=Cormorant+Garamond:wght@500;600&family=Cormorant+SC:wght@500&display=swap">
<style>
  :root {
    --sky-top: #8fd0ef;
    --sky-mid: #d9f0fa;
    --haze: #eef7fb;
    --sea: #3d8fc2;
    --sea-deep: #1f6a9e;
    --city: #c9b49a;
    --green: #5d7a45;
    --copper: #b06f55;
    --ink: #1b1b1b;
    --band: #0c0c0c;
    --band-text: #ffffff;
  }
  * { margin: 0; padding: 0; box-sizing: border-box; }
  html, body { width: 855px; height: 1200px; overflow: hidden; background: #fff; }
  .poster { position: relative; width: 855px; height: 1200px; overflow: hidden; }

  .harbour-photo {
    position: absolute; inset: 0 0 108px 0;
    background:
      radial-gradient(ellipse 60% 35% at 78% 78%, rgba(201,180,154,.95), rgba(201,180,154,0) 70%),
      radial-gradient(ellipse 35% 30% at 95% 62%, rgba(93,122,69,.7), rgba(93,122,69,0) 70%),
      radial-gradient(ellipse 40% 18% at 30% 92%, rgba(93,122,69,.55), rgba(93,122,69,0) 70%),
      linear-gradient(180deg, var(--sky-top) 0%, var(--sky-mid) 22%, var(--haze) 42%, #b7d9ec 52%, var(--sea) 66%, var(--sea-deep) 100%);
  }

  .brand {
    position: absolute; top: 168px; left: 0; right: 0;
    display: flex; justify-content: center; align-items: center; gap: 18px;
  }
  .brand-square { width: 26px; height: 26px; background: var(--copper); }
  .brand-name {
    font-family: "Cormorant Garamond", serif; font-weight: 600;
    font-size: 58px; letter-spacing: 6px; color: var(--copper); text-transform: uppercase;
  }

  .tagline {
    position: absolute; top: 378px; left: 0; right: 0;
    font-family: "Cormorant SC", serif; font-weight: 500; color: var(--ink);
    font-size: 48px; line-height: 1.15; letter-spacing: 1px;
  }
  .tagline span { display: block; }
  .tagline .line-one { padding-left: 270px; }
  .tagline .line-two { padding-left: 368px; }

  .contact-band {
    position: absolute; left: 0; right: 0; bottom: 0; height: 108px;
    background: var(--band); color: var(--band-text);
    font-family: "Cormorant Garamond", serif; font-weight: 600;
    font-size: 27px; line-height: 1.3; text-align: center;
    display: flex; flex-direction: column; justify-content: center;
  }
  .contact-band .sep { margin: 0 14px; }
</style>
</head>
<body>
<main class="poster">
  <div class="harbour-photo" role="img" aria-label="Aerial view of Monaco: pale sky, blue sea and harbour, dense city towers and green hillside"></div>

  <header class="brand">
    <span class="brand-square" aria-hidden="true"></span>
    <span class="brand-name">Corvano Immo</span>
  </header>

  <h1 class="tagline">
    <span class="line-one">Un nouveau regard</span>
    <span class="line-two">sur l'immobilier</span>
  </h1>

  <footer class="contact-band">
    <p class="address">14 rue des Ormeaux, Galerie Bellerive Nord, &nbsp;98 000 Monaco</p>
    <p class="reach">+377.93.48.25.07<span class="sep">|</span>www.corvano-immo.com</p>
  </footer>
</main>
</body>
</html>
```